Varnel Corporate Website for technological company

We need a modern website to promote our product and services.
You can found the actually website at the address: www.varnel-example.ch

We are a new company for B2B market. We would like do show our high precision and innovation capability.

we need a section were is possible to easily upload "news" and documents for our customers.

Target Market(s)

B2B services in the industry market

Industry/Entity Type

It Company

Coding

Coded - Design and coding required

Number of Pages Required

5+ page

Font styles to use
Other font styles liked:
• We accept propositions

Requirements
Must have
• Easy to maintain
• Presentation of the Varnel company
• Presentation of Varnel services and products
• The customer can download our ducumentation
Nice to have
• Sexy and modern

```html
<!DOCTYPE html>
<html lang="en">
<head>
<meta charset="utf-8">
<title>Varnel Ltd – Integrated Electronics, Software and Mechanics</title>
<link rel="stylesheet" href="https://fonts.googleapis.com/css2?family=Open+Sans:ital,wght@0,400;0,600;0,700;1,400&family=Play:wght@400;700&display=swap">
<style>
:root{
  --olive:#b1a56a;
  --olive-dark:#9c9157;
  --ink:#2b2b2b;
  --text:#555;
  --muted:#8a8a8a;
  --line:#e3e3e3;
  --paper:#fff;
  --grey-band:#f2f2f2;
  --footer:#1c1c1c;
  --heading:"Play",sans-serif;
  --body:"Open Sans",sans-serif;
}
*{box-sizing:border-box;margin:0;padding:0}
html,body{width:1200px;height:2663px;overflow:hidden}
body{font-family:var(--body);color:var(--text);background:var(--paper);position:relative}
a{color:inherit;text-decoration:none}
ul{list-style:none}

/* top bar */
.topbar{height:30px;background:var(--olive);color:#fff;font-size:12px;display:flex;align-items:center;justify-content:space-between;padding:0 98px 0 98px}
.topbar .call{display:flex;align-items:center;gap:8px}
.topbar .restricted{display:flex;align-items:center;height:30px;font-size:11px;text-transform:uppercase;letter-spacing:.5px}
.topbar .restricted span,.topbar .restricted a{padding:0 16px;display:flex;align-items:center;gap:6px;height:30px;border-left:1px solid rgba(255,255,255,.35)}
.topbar .restricted span{border-left:none}

/* header */
.header{height:86px;display:flex;align-items:center;justify-content:space-between;padding:0 98px}
.brand{display:flex;align-items:center;gap:10px;font-family:var(--heading);font-weight:700;font-size:30px;color:var(--ink);letter-spacing:1px}
.brand .mark{width:22px;height:22px;background:var(--olive)}
.nav{display:flex;gap:6px;font-size:13px;text-transform:uppercase;color:var(--ink)}
.nav a{padding:8px 14px}
.nav a.active{background:var(--olive);color:#fff}

/* hero */
.hero{position:relative;height:514px;background:
  radial-gradient(ellipse 280px 220px at 720px 250px,rgba(200,140,60,.55),transparent 70%),
  radial-gradient(ellipse 200px 200px at 560px 330px,rgba(80,150,90,.45),transparent 70%),
  radial-gradient(ellipse 220px 180px at 820px 180px,rgba(170,60,70,.45),transparent 70%),
  linear-gradient(90deg,#6c6a66 0%,#8e8c88 40%,#b3b1ad 100%)}
.hero .arrow{position:absolute;top:230px}
.hero .arrow.prev{left:44px}
.hero .arrow.next{right:44px}

/* welcome */
.welcome{height:408px;position:relative}
.welcome .copy{position:absolute;left:98px;top:55px;width:630px}
.welcome h1{font-family:var(--heading);font-weight:400;font-size:29px;color:var(--ink);margin-bottom:18px;letter-spacing:.5px}
.welcome p{font-size:11.2px;line-height:21px;margin-bottom:10px}
.welcome h3{font-size:12.5px;font-weight:600;color:#444;margin:4px 0 8px}
.welcome li{font-size:11.2px;line-height:21px;display:flex;align-items:center;gap:10px}
.welcome li::before{content:"";width:6px;height:6px;border-radius:50%;border:1.5px solid #777}
.welcome .sketch{position:absolute;left:781px;top:45px;width:311px;height:363px;background:linear-gradient(160deg,#fff 40%,#f4e4d6 75%,#e8c3a6 100%)}

/* services */
.services{height:478px;position:relative;background:linear-gradient(var(--olive) 0,var(--olive) 240px,var(--paper) 240px)}
.section-title{font-family:var(--heading);font-weight:700;font-size:30px;text-align:center;letter-spacing:.5px}
.services .section-title{color:#fff;padding-top:38px}
.cards{position:absolute;left:98px;top:164px;display:flex;gap:20px}
.card{width:236px;height:239px;background:#fafafa;border:1px solid #ececec;box-shadow:0 2px 3px rgba(0,0,0,.06);text-align:center;position:relative;padding-top:72px}
.card .badge{position:absolute;left:61px;top:-57px;width:114px;height:114px;border-radius:50%;background:var(--olive);border:6px solid var(--paper);display:flex;align-items:center;justify-content:center}
.card h3{font-family:var(--heading);font-weight:400;font-size:18px;color:var(--ink);margin-bottom:10px}
.card p{font-size:11.4px;line-height:20px;padding:0 22px;height:62px;overflow:hidden}
.card .more{display:inline-block;margin-top:15px;border:1px solid #777;font-size:11.5px;padding:5px 12px;color:#444;text-transform:uppercase}

/* products */
.products{height:309px;position:relative}
.products .section-title{color:var(--ink);font-weight:400;padding-top:13px}
.product-row{position:absolute;left:98px;top:50px;display:flex;gap:20px}
.product{width:236px;height:202px;background:linear-gradient(#dcdcdc,#c8c8c8)}
.products .product-row{top:98px}

/* blog */
.blog{height:491px;background:var(--grey-band);position:relative}
.blog .section-title{color:var(--ink);font-weight:400;padding-top:43px}
.blog .rule{width:80px;height:1px;background:#bbb;margin:10px auto 0}
.posts{position:absolute;left:98px;top:128px;display:flex;gap:32px}
.post{width:314px}
.post .photo{height:163px}
.post h4{font-weight:400;font-size:15.5px;color:#444;margin:17px 0 12px}
.post .meta{display:flex;gap:28px;font-size:11.5px;font-style:italic;color:var(--muted);margin-bottom:14px}
.post .meta span{display:flex;align-items:center;gap:7px}
.post p{font-size:11.2px;line-height:20px}

/* footer */
.footer{height:290px;background:linear-gradient(#151515,#262626);color:#ddd;position:relative;font-size:12px}
.footer h5{font-weight:400;font-size:15.5px;color:#fff;text-transform:uppercase;margin-bottom:18px}
.col{position:absolute;top:46px}
.col.contact{left:98px;width:300px}
.col.links{left:449px}
.col.news{left:658px;width:258px}
.col.social{left:1006px}
.contact address{font-style:normal;line-height:20px;margin-bottom:12px}
.contact .row{display:flex;gap:18px;align-items:center;line-height:19px;margin-bottom:10px}
.links li{line-height:23px;display:flex;align-items:center;gap:10px;font-size:11.5px}
.links li::before{content:"";border-left:5px solid #ddd;border-top:4px solid transparent;border-bottom:4px solid transparent}
.news p{font-size:11px;line-height:19px;margin-bottom:14px}
.news .field{width:255px;height:40px;background:#fff;color:#666;font-size:11px;padding:0 14px;display:flex;align-items:center}
.news .subscribe{display:inline-block;margin-top:10px;background:var(--olive);color:#fff;font-size:11.5px;padding:12px 15px;text-transform:uppercase}
.social li{display:flex;align-items:center;gap:9px;margin-bottom:11px;font-size:13px}
.social li::before{content:"";width:26px;height:26px;border-radius:50%;border:1.5px solid #ddd}

.bottombar{height:57px;background:var(--olive);color:#fff;font-size:11.5px;display:flex;align-items:center;justify-content:space-between;padding:0 24px 0 98px}
.bottombar nav{display:flex;gap:8px}
.bottombar .tag{margin-left:40px}
</style>
</head>
<body>

<div class="topbar">
  <div class="call">
    <svg width="12" height="12" viewBox="0 0 24 24" fill="#fff"><path d="M6.6 10.8a15 15 0 0 0 6.6 6.6l2.2-2.2a1 1 0 0 1 1-.25 11.4 11.4 0 0 0 3.6.57 1 1 0 0 1 1 1V20a1 1 0 0 1-1 1A17 17 0 0 1 3 4a1 1 0 0 1 1-1h3.5a1 1 0 0 1 1 1c0 1.25.2 2.45.57 3.6a1 1 0 0 1-.25 1z"/></svg>
    Call now for more information 1300 482 907
  </div>
  <div class="restricted">
    <span>Restricted :</span>
    <a href="#">
      <svg width="10" height="12" viewBox="0 0 10 12" fill="#fff"><rect x="0" y="5" width="10" height="7" rx="1"/><path d="M2.5 5V3.5a2.5 2.5 0 0 1 5 0V5" stroke="#fff" stroke-width="1.5" fill="none"/></svg>
      Login
    </a>
    <a href="#">
      <svg width="11" height="11" viewBox="0 0 12 12" fill="#fff"><circle cx="6" cy="3.5" r="3"/><path d="M0 12a6 5 0 0 1 12 0z"/></svg>
      Mail
    </a>
  </div>
</div>

<header class="header">
  <a class="brand" href="#"><span class="mark"></span>Varnel</a>
  <nav class="nav">
    <a class="active" href="#">Home</a>
    <a href="#">Services</a>
    <a href="#">Products</a>
    <a href="#">Examples</a>
    <a href="#">Download</a>
    <a href="#">Contacts</a>
  </nav>
</header>

<section class="hero" role="img" aria-label="Photo of a businessman touching colourful puzzle pieces labelled process, structure, risk, information, governance, privacy, policy, control, compliance and procedure">
  <svg class="arrow prev" width="22" height="56" viewBox="0 0 22 56"><path d="M20 2 2 28l18 26" stroke="#fff" stroke-width="1.5" fill="none"/></svg>
  <svg class="arrow next" width="22" height="56" viewBox="0 0 22 56"><path d="M2 2l18 26L2 54" stroke="#fff" stroke-width="1.5" fill="none"/></svg>
</section>

<section class="welcome">
  <div class="copy">
    <h1>WELCOME TO VARNEL LTD</h1>
    <p>The ever-increasing complexity in modern systems, the search for reliability and performance and the continuous desire to reduce production costs and dimensions of the products require a rigorous integration between the electronic units, software and mechanical systems. Varnel Ltd. designs systems in which electronics, software and mechanics are perfectly integrated to achieve uncompromising performance.</p>
    <p>Varnel Ltd. can develop complete solutions or intervene at a later stage of the product development to carry out studies and / or produce units that will be integrated into your processes, machines or products.</p>
    <h3>Varnel Ltd. is a company active in the following areas:</h3>
    <ul>
      <li>Simulation and modeling of complete processes</li>
      <li>Concept and design of electronic circuits and mechanical units</li>
      <li>Development of application specific control software</li>
      <li>Rapid prototyping (electronic cards, mechanisms ...)</li>
    </ul>
  </div>
  <div class="sketch" role="img" aria-label="Illustration of a hand drawing a glowing light bulb with a marker"></div>
</section>

<section class="services">
  <h2 class="section-title">OUR SERVICES</h2>
  <div class="cards">
    <article class="card">
      <div class="badge">
        <svg width="40" height="40" viewBox="0 0 40 40" fill="none" stroke="#fff" stroke-width="2.5"><path d="M20 5a10 10 0 0 0-6 18v5h12v-5A10 10 0 0 0 20 5z"/><path d="M15 32h10M16 36h8"/></svg>
      </div>
      <h3>Simulation &amp; Modeling</h3>
      <p>Through a multi-physics modelling approach, Varnel Ltd. can integrate into the simulation</p>
      <a class="more" href="#">Read more</a>
    </article>
    <article class="card">
      <div class="badge">
        <svg width="42" height="42" viewBox="0 0 42 42" fill="none" stroke="#fff" stroke-width="2.5"><rect x="10" y="10" width="22" height="22" rx="2"/><rect x="16" y="16" width="10" height="10"/><path d="M15 4v6M21 4v6M27 4v6M15 32v6M21 32v6M27 32v6M4 15h6M4 21h6M4 27h6M32 15h6M32 21h6M32 27h6"/></svg>
      </div>
      <h3>Electronics</h3>
      <p>Varnel Sàrl being active in all fields associated with actuator electronics, can develop solutions integrating</p>
      <a class="more" href="#">Read more</a>
    </article>
    <article class="card">
      <div class="badge">
        <svg width="44" height="44" viewBox="0 0 44 44" fill="#fff"><circle cx="17" cy="24" r="11"/><circle cx="17" cy="24" r="4" fill="var(--olive)"/><g stroke="#fff" stroke-width="5"><path d="M17 9v30M2 24h30M6.4 13.4l21.2 21.2M27.6 13.4 6.4 34.6"/></g><circle cx="33" cy="11" r="6"/><circle cx="33" cy="11" r="2.2" fill="var(--olive)"/><g stroke="#fff" stroke-width="3"><path d="M33 2v18M24 11h18"/></g></svg>
      </div>
      <h3>Mechanics</h3>
      <p>Varnel Ltd. is able to design and build mechanisms, assembly groups and custom devices from</p>
      <a class="more" href="#">Read more</a>
    </article>
    <article class="card">
      <div class="badge">
        <svg width="42" height="34" viewBox="0 0 42 34" fill="none" stroke="#fff" stroke-width="3.5" stroke-linecap="round" stroke-linejoin="round"><path d="M12 8 3 17l9 9M30 8l9 9-9 9M24 3l-6 28"/></svg>
      </div>
      <h3>Software</h3>
      <p>Modern electrical systems are built around microcontrollers and other logic units that require the development</p>
      <a class="more" href="#">Read more</a>
    </article>
  </div>
</section>

<section class="products">
  <h2 class="section-title">OUR PRODUCTS</h2>
  <div class="product-row">
    <div class="product" role="img" aria-label="Photo of a green circuit board with a blue chip"></div>
    <div class="product" role="img" aria-label="Photo of a small black electronic enclosure"></div>
    <div class="product" role="img" aria-label="Photo of a compact green controller board"></div>
    <div class="product" role="img" aria-label="Photo of a black sensor unit with cable next to a circuit board"></div>
  </div>
</section>

<section class="blog">
  <h2 class="section-title">LATEST BLOG</h2>
  <div class="rule"></div>
  <div class="posts">
    <article class="post">
      <div class="photo" role="img" aria-label="Photo of a precision optical test bench" style="background:linear-gradient(135deg,#2e2e2e,#6b6b6b 55%,#3b4a66)"></div>
      <h4>Nemo enim ipsam voluptatem quia</h4>
      <div class="meta">
        <span><svg width="11" height="11" viewBox="0 0 12 12" fill="#999"><rect x="0" y="2" width="12" height="10" rx="1"/><rect x="1.5" y="5" width="9" height="5.5" fill="#f2f2f2"/></svg>March 25, 2016</span>
        <span><svg width="12" height="11" viewBox="0 0 12 11" fill="none" stroke="#999" stroke-width="1.3"><path d="M1 1h10v7H5l-3 2V8H1z"/></svg>No comments</span>
      </div>
      <p>Lorem ipsum dolor sit amet, consectetur adipiscing elit, sed do eiusmod tempor incididunt ut labore et dolore magna aliqua. Ut enim ad minim veniam,</p>
    </article>
    <article class="post">
      <div class="photo" role="img" aria-label="Photo of a gloved hand testing a circuit board" style="background:linear-gradient(135deg,#2f5a2f,#6d9a4e 50%,#c8c8b8)"></div>
      <h4>Nemo enim ipsam voluptatem quia</h4>
      <div class="meta">
        <span><svg width="11" height="11" viewBox="0 0 12 12" fill="#999"><rect x="0" y="2" width="12" height="10" rx="1"/><rect x="1.5" y="5" width="9" height="5.5" fill="#f2f2f2"/></svg>March 25, 2016</span>
        <span><svg width="12" height="11" viewBox="0 0 12 11" fill="none" stroke="#999" stroke-width="1.3"><path d="M1 1h10v7H5l-3 2V8H1z"/></svg>No comments</span>
      </div>
      <p>Lorem ipsum dolor sit amet, consectetur adipiscing elit, sed do eiusmod tempor incididunt ut labore et dolore magna aliqua. Ut enim ad minim veniam,</p>
    </article>
    <article class="post">
      <div class="photo" role="img" aria-label="Photo of black and yellow mechanical gears" style="background:linear-gradient(135deg,#111,#3a3a3a 50%,#c9a51e 75%,#8c8c8c)"></div>
      <h4>Nemo enim ipsam voluptatem quia</h4>
      <div class="meta">
        <span><svg width="11" height="11" viewBox="0 0 12 12" fill="#999"><rect x="0" y="2" width="12" height="10" rx="1"/><rect x="1.5" y="5" width="9" height="5.5" fill="#f2f2f2"/></svg>March 25, 2016</span>
        <span><svg width="12" height="11" viewBox="0 0 12 11" fill="none" stroke="#999" stroke-width="1.3"><path d="M1 1h10v7H5l-3 2V8H1z"/></svg>No comments</span>
      </div>
      <p>Lorem ipsum dolor sit amet, consectetur adipiscing elit, sed do eiusmod tempor incididunt ut labore et dolore magna aliqua. Ut enim ad minim veniam,</p>
    </article>
  </div>
</section>

<footer class="footer">
  <div class="col contact">
    <h5>Contact us</h5>
    <address>VARNEL LTD Chemin des Vergers 8<br>CH - 1690 Villaz</address>
    <div class="row">
      <svg width="16" height="16" viewBox="0 0 24 24" fill="none" stroke="#ddd" stroke-width="1.6"><path d="M6.6 10.8a15 15 0 0 0 6.6 6.6l2.2-2.2a1 1 0 0 1 1-.25 11.4 11.4 0 0 0 3.6.57 1 1 0 0 1 1 1V20a1 1 0 0 1-1 1A17 17 0 0 1 3 4a1 1 0 0 1 1-1h3.5a1 1 0 0 1 1 1c0 1.25.2 2.45.57 3.6a1 1 0 0 1-.25 1z"/></svg>
      <div>Phone : +41 (0)26 555 01 42<br>&nbsp;&nbsp;&nbsp;&nbsp;&nbsp;&nbsp;Fax : +607 5550 2198</div>
    </div>
    <div class="row">
      <svg width="16" height="12" viewBox="0 0 16 12" fill="none" stroke="#ddd" stroke-width="1.4"><rect x="1" y="1" width="14" height="10"/><path d="M1 1l7 6 7-6"/></svg>
      <div>Email: info@varnel.ch</div>
    </div>
  </div>
  <div class="col links">
    <h5>Quick links</h5>
    <ul>
      <li>Home</li><li>Services</li><li>Products</li><li>Examples</li><li>Download</li><li>Contacts</li>
    </ul>
  </div>
  <div class="col news">
    <h5>Join our newsletter</h5>
    <p>Sed ut perspiciatis unde omnis iste natus error sit voluptatem accusantium dolore</p>
    <div class="field">Enter Email</div>
    <a class="subscribe" href="#">Subscribe</a>
  </div>
  <div class="col social">
    <h5>Social</h5>
    <ul>
      <li>Friendlyn</li><li>Chirpa</li><li>Circlo</li><li>Clipstream</li>
    </ul>
  </div>
</footer>

<div class="bottombar">
  <span>Copyright 2016 | All Rights Reserved – VARNEL LTD</span>
  <div style="display:flex;align-items:center">
    <nav><a href="#">Sitemap</a>/<a href="#">Terms of Use</a>/<a href="#">Privacy Policy</a></nav>
    <span class="tag">C7</span>
  </div>
</div>

</body>
</html>
```